BRISKLY sparkling water needs new artwork! Based in Southern California

"Briskly" is a new sparkling water company based in Southern California that offers refreshing flavors (lime, cherry, & mango) with B vitamins and antioxidants.

We would like to see packaging designs for standard 12oz cans for each of the three flavors.
Our initial preference is to have individual artwork for each flavor.

Attached are examples of competitors' designs.
Updates

We are extending the deadline for the Thanksgiving Holiday. Thank you all for your contributions.

```html
<!DOCTYPE html>
<html lang="en">
<head>
<meta charset="utf-8">
<title>Briskly Sparkling Water – Mango Can Label</title>
<link rel="stylesheet" href="https://fonts.googleapis.com/css2?family=Fredoka:wght@500;600;700&display=swap">
<style>
  :root {
    --backdrop: #ececec;
    --gold-deep: #d4940f;
    --gold-mid: #efb423;
    --gold-light: #f8cf4f;
    --ink: #2d2d2d;
    --panel: #f7f7f2;
    --teal: #4a9488;
    --teal-light: #6fb2a6;
    --mango-light: #fbe38a;
    --mango-mid: #f3c54a;
    --white: #ffffff;
  }
  * { box-sizing: border-box; margin: 0; padding: 0; }
  html, body {
    width: 1174px;
    height: 1200px;
    overflow: hidden;
    background: var(--backdrop);
  }
  .stage {
    position: relative;
    width: 1174px;
    height: 1200px;
    font-family: "Fredoka", sans-serif;
  }
  .label {
    position: absolute;
    left: 307px;
    top: 150px;
    width: 560px;
    height: 900px;
    border-radius: 14px;
    overflow: hidden;
    background: linear-gradient(90deg, var(--gold-deep) 0%, var(--gold-mid) 30%, var(--gold-light) 55%, var(--gold-mid) 78%, var(--gold-deep) 100%);
  }
  .brand-name {
    position: absolute;
    left: 0;
    top: 150px;
    width: 100%;
    text-align: center;
    font-weight: 700;
    font-size: 96px;
    line-height: 1;
    color: var(--ink);
  }
  .title-panel {
    position: absolute;
    left: 53px;
    top: 280px;
    width: 454px;
    height: 290px;
    background: var(--panel);
    border: 6px solid var(--ink);
    border-radius: 70px;
    display: flex;
    flex-direction: column;
    align-items: center;
    justify-content: center;
    padding-bottom: 30px;
    color: var(--ink);
    font-weight: 600;
    line-height: 0.95;
  }
  .title-panel .line-one { font-size: 80px; letter-spacing: 1px; }
  .title-panel .line-two { font-size: 104px; letter-spacing: 2px; }
  .benefit-band {
    position: absolute;
    left: 30px;
    top: 540px;
    width: 500px;
    height: 46px;
    background: var(--teal-light);
    color: var(--white);
    font-weight: 500;
    font-size: 19px;
    letter-spacing: 0.5px;
    display: flex;
    align-items: center;
    justify-content: center;
    text-transform: uppercase;
  }
  .fruit-art {
    position: absolute;
    left: 30px;
    top: 640px;
    width: 230px;
    height: 230px;
    border-radius: 50%;
    background: radial-gradient(circle at 40% 40%, var(--mango-light) 0%, var(--mango-mid) 80%);
  }
  .flavor-badge {
    position: absolute;
    left: 300px;
    top: 650px;
    width: 230px;
    height: 150px;
    background: var(--teal);
    border-radius: 40px 40px 40px 10px;
    color: var(--white);
    display: flex;
    flex-direction: column;
    align-items: center;
    justify-content: center;
    font-weight: 600;
    line-height: 1;
  }
  .flavor-badge .flavor-name { font-size: 56px; }
  .flavor-badge .flavor-word { font-size: 34px; margin-top: 6px; }
</style>
</head>
<body>
  <main class="stage">
    <section class="label">
      <div class="brand-name">Briskly</div>

      <div class="title-panel">
        <span class="line-one">SPARKLING</span>
        <span class="line-two">WATER</span>
      </div>

      <div class="benefit-band">With B vitamins and antioxidants</div>

      <div class="fruit-art" role="img" aria-label="Illustration of a ripe mango with leaves"></div>

      <div class="flavor-badge">
        <span class="flavor-name">MANGO</span>
        <span class="flavor-word">FLAVOR</span>
      </div>
    </section>
  </main>
</body>
</html>
```